Jolly Paws Business Card Update

I have a business card which I love. I want to keep the same logo, colours, font and style. I want to upgrade the scripting and remove some elements and add others.
On the front side under Services - remove the existing wording and insert - Providing individual coaching strategies to create happy, healthy and social canine companions
Under Denise Carvell amend the current wording to read: Qualified in Dog Behavioural Training, Natural Animal Healthcare and Animal Health Science
On the reverse side to remove the web address.

```html
<!DOCTYPE html>
<html lang="en">
<head>
<meta charset="utf-8">
<title>Jolly Paws Business Card</title>
<link rel="stylesheet" href="https://fonts.googleapis.com/css2?family=Ubuntu:wght@400;500;700&family=Open+Sans:ital,wght@1,400&family=Arimo:wght@400;700&display=swap">
<style>
  :root {
    --page-bg: #e4e1dc;
    --card-bg: #f4f3f1;
    --card-bg-edge: #e9e8e6;
    --navy: #2b3a8f;
    --brand-blue: #2f6db5;
    --brand-red: #b3262c;
    --brand-red-deep: #861a1f;
    --services-text: #f5dcd4;
  }
  * { margin: 0; padding: 0; box-sizing: border-box; }
  html, body { width: 1200px; height: 1054px; overflow: hidden; }
  body { background: var(--page-bg); position: relative; }

  .business-card {
    position: absolute;
    left: 100px; top: 227px;
    width: 1000px; height: 600px;
    border-radius: 24px;
    overflow: hidden;
    background: linear-gradient(160deg, var(--card-bg) 0%, var(--card-bg-edge) 100%);
    box-shadow: 0 10px 30px rgba(0,0,0,0.15);
  }

  .accent-band {
    position: absolute; left: 0; right: 0; top: 410px; bottom: 0;
    background: linear-gradient(180deg, var(--brand-blue) 0px, var(--brand-blue) 10px, var(--card-bg) 10px, var(--card-bg) 22px, var(--brand-red) 22px, var(--brand-red-deep) 100%);
  }

  .holder-name {
    position: absolute; left: 66px; top: 70px;
    font-family: "Ubuntu", sans-serif; font-weight: 500;
    font-size: 39px; color: var(--navy); letter-spacing: 0.2px;
  }
  .qualifications {
    position: absolute; left: 66px; top: 128px;
    font-family: "Open Sans", sans-serif; font-style: italic;
    font-size: 22.5px; line-height: 34px; color: var(--navy);
  }
  .contact-list {
    position: absolute; left: 66px; top: 270px;
    list-style: none;
    font-family: "Ubuntu", sans-serif; font-size: 24px; color: var(--navy);
  }
  .contact-item { display: flex; align-items: center; height: 37px; }
  .contact-icon { width: 22px; height: 22px; margin-right: 22px; fill: var(--brand-red); }

  .brand-name {
    position: absolute; right: 70px; top: 150px;
    font-family: "Ubuntu", sans-serif; font-weight: 500;
    font-size: 36px; color: var(--navy);
  }

  .services {
    position: absolute; right: 40px; top: 450px;
    text-align: right; font-family: "Arimo", sans-serif;
    color: var(--services-text); font-size: 23px; line-height: 31px;
  }
  .services-title { font-weight: 700; font-size: 24px; }
</style>
</head>
<body>
  <div class="business-card">
    <div class="accent-band" role="img" aria-label="Decorative blue and red wave band"></div>

    <h1 class="holder-name">Denise Carvell</h1>
    <p class="qualifications">Qualified in Dog Behavioural Training,<br>Natural Animal Healthcare and<br>Animal Health Science</p>

    <ul class="contact-list">
      <li class="contact-item">
        <svg class="contact-icon" viewBox="0 0 22 22"><rect x="6" y="1" width="10" height="20" rx="2"/><rect x="8" y="4" width="6" height="5" fill="#f4f3f1"/></svg>
        0412 555 208
      </li>
      <li class="contact-item">
        <svg class="contact-icon" viewBox="0 0 22 22"><rect x="1" y="5" width="20" height="13"/><path d="M1 5 L11 13 L21 5" fill="none" stroke="#f4f3f1" stroke-width="2"/></svg>
        jollypaws1@mailbox.com
      </li>
      <li class="contact-item">
        <svg class="contact-icon" viewBox="0 0 22 22"><circle cx="11" cy="11" r="9"/><path d="M2 11 H20 M11 2 C6 7 6 15 11 20 M11 2 C16 7 16 15 11 20" fill="none" stroke="#f4f3f1" stroke-width="1.5"/></svg>
        www.jollypaws1.com
      </li>
    </ul>

    <p class="brand-name">Jolly Paws</p>

    <div class="services">
      <p class="services-title">SERVICES:</p>
      <p>Providing Individual Coaching<br>Strategies to Create Happy,<br>Healthy &amp; Social Canine Companions</p>
    </div>
  </div>
</body>
</html>
```